Website for "Bright Morrow Ltd" cleaning bsuiness

We require a website to expose our business to the local market. We want to provide background on who we are and what we do but in an easily digestible way. We clean domestic and commercial premises and want to provide a list of all of our services to potential customers. We operate out of Warrington in the UK.

We would like the website to be animated in some way so that the experience of using it is not dull or mundane. This website needs to be an extension of our company.

Target Market(s)

30 - 60 year olds for Domestic plus commercial clients

Industry/Entity Type

Cleaning Service

Coding

Coded - Design and coding required

Number of Pages Required

4 page

Font styles to use
Sans Serif

Colors
0455a3
3176b5
85acd3
cfdeed
ffffff
000000
1b1b1b
c8c8c8
757575

Requirements
Must have
• Logo which has been provided. Theme based around the logo and its colours. Simple layout to avoid confusion.
Nice to have
• Animations where possible to impress the customer.
Should not have
• any pictures of cleaning equipment, fairies, maids etc

```html
<!DOCTYPE html>
<html lang="en">
<head>
<meta charset="utf-8">
<title>Bright Morrow Ltd – Cleaning Services in Warrington</title>
<link rel="stylesheet" href="https://fonts.googleapis.com/css2?family=Open+Sans:wght@600;700&family=Roboto:wght@400;500;700&display=swap">
<style>
:root{
  --blue-deep:#0455a3;
  --blue-mid:#3176b5;
  --blue-soft:#85acd3;
  --blue-pale:#cfdeed;
  --white:#ffffff;
  --black:#000000;
  --charcoal:#1b1b1b;
  --silver:#c8c8c8;
  --grey:#757575;
  --ink:#333333;
  --head:'Open Sans',Arial,sans-serif;
  --body:'Roboto',Arial,sans-serif;
}
*{margin:0;padding:0;box-sizing:border-box}
html,body{width:1200px;height:2699px;overflow:hidden;background:var(--white)}
body{font-family:var(--body);color:var(--ink)}
.page{position:relative;width:1200px;height:2699px;overflow:hidden}
.abs{position:absolute}
a{color:inherit;text-decoration:none}

/* hero */
.hero{left:0;top:0;width:1200px;height:600px;
  background:linear-gradient(180deg,#0b1f4a 0%,#163a7a 30%,#2a5a9e 48%,#1a2f55 62%,#2b4f85 78%,#0e1f3f 100%)}
.brand{font-family:var(--head);font-weight:700;color:var(--blue-mid);line-height:1.05;display:flex;align-items:center;gap:14px}
.brand-dot{width:22px;height:22px;border-radius:50%;background:var(--blue-mid);flex:none}
.hero .brand{left:150px;top:46px;font-size:38px;color:var(--white)}
.hero .brand .brand-dot{background:var(--white)}
.contact-chip{display:flex;align-items:center;gap:14px;color:var(--white)}
.chip-icon{width:34px;height:34px;border-radius:50%;border:2px solid var(--white);display:flex;align-items:center;justify-content:center}
.chip-label{font-size:10px;font-weight:700;letter-spacing:.5px}
.chip-value{font-size:14px}
.chip-value.strong{font-size:16px;font-weight:700}
.main-nav{top:92px;left:511px;display:flex;align-items:center;gap:0}
.main-nav a{font-size:12.5px;font-weight:700;color:var(--white);text-transform:uppercase;padding:8px 10px;margin-right:30px}
.main-nav a.active{background:var(--white);color:var(--blue-deep)}
.hero-title{left:0;width:1210px;top:388px;text-align:center;color:var(--white);font-family:var(--head);font-weight:700;text-transform:uppercase;text-shadow:0 2px 6px rgba(0,0,0,.4)}
.hero-title h1{font-size:40px;line-height:48px}
.hero-title p{font-size:23px;line-height:30px}
.slider-ctrl{left:564px;top:490px;width:62px;height:36px;border-radius:18px;background:var(--blue-deep);display:flex;align-items:center;justify-content:center;gap:12px}

/* headings */
.section-title{font-family:var(--head);font-weight:700;font-size:24px;text-transform:uppercase;text-align:center}
.rule{height:3px;width:80px}

/* services */
.services-title{left:0;width:1200px;top:572px;color:var(--blue-deep)}
.services-rule{left:562px;top:616px;background:var(--blue-deep)}
.service{display:flex;align-items:center;gap:22px;font-size:15px;line-height:21px;color:var(--ink)}
.service-icon{width:52px;height:52px;border-radius:50%;border:2px solid var(--blue-deep);display:flex;align-items:center;justify-content:center;flex:none}
.divider{width:1px;height:274px;top:675px;background:#e2e2e2}

/* who we are */
.about-photo{left:0;top:999px;width:594px;height:470px;
  background:linear-gradient(160deg,#3e7ccc 0%,#6fa3de 35%,#b7d2ef 55%,#4a84c8 80%,#2f66ad 100%)}
.about-panel{left:599px;top:999px;width:601px;height:470px;background:var(--blue-deep)}
.about-title{left:668px;top:1046px;color:var(--white);font-family:var(--head);font-weight:700;font-size:24px}
.about-rule{left:668px;top:1091px;background:var(--white)}
.about-lead{left:668px;top:1127px;width:404px;color:var(--white);font-size:14.5px;line-height:21px;font-weight:700;text-align:justify}
.about-body{left:668px;top:1191px;width:404px;color:var(--white);font-size:14px;line-height:21.5px;text-align:justify}
.btn{font-family:var(--body);font-weight:700;text-transform:uppercase;color:var(--white);border:0;display:flex;align-items:center;justify-content:center}
.btn-more{left:671px;top:1307px;width:110px;height:36px;background:var(--blue-mid);font-size:12px}

/* what we do */
.work{left:0;top:1440px;width:1200px;height:560px;background:var(--blue-mid)}
.work-title{left:0;width:1200px;top:1466px;color:var(--white)}
.work-rule{left:562px;top:1512px;background:var(--white)}
.step-line{left:175px;top:1640px;height:210px;border-left:2px dashed var(--blue-pale)}
.step-dot{width:86px;height:86px;border-radius:50%;background:var(--white);display:flex;align-items:center;justify-content:center}
.step-head{font-family:var(--head);font-weight:700;font-size:14px;color:var(--white);text-transform:uppercase}
.step-text{font-size:13px;line-height:19px;color:var(--white);width:300px;margin-top:6px}

/* quote */
.quote{left:0;top:1992px;width:1200px;height:360px;background:var(--charcoal)}
.quote-title{left:133px;top:2049px;font-family:var(--head);font-weight:700;font-size:25px;color:var(--blue-deep)}
.quote-rule{left:133px;top:2090px;width:133px;background:var(--blue-deep)}
.quote-text{left:133px;top:2122px;width:360px;font-size:13px;line-height:24px;color:var(--grey)}
.field{background:var(--white);border-radius:2px;font-size:11px;color:var(--ink);padding:0 14px;display:flex;align-items:center}
.field.area{align-items:flex-start;padding-top:18px}
.btn-submit{left:950px;top:2234px;width:119px;height:38px;background:var(--blue-deep);font-size:13px;border-radius:2px}

/* footer */
.footer{left:0;top:2320px;width:1200px;height:310px;background:var(--blue-deep)}
.footer .brand{left:135px;top:2405px;font-size:34px;color:var(--white)}
.footer .brand .brand-dot{background:var(--white)}
.foot-head{font-family:var(--head);font-weight:700;font-size:12.5px;color:var(--white);text-transform:uppercase}
.foot-list{list-style:none;font-size:12px;line-height:24px;color:var(--white);margin-top:16px}
.news-field{left:772px;top:2430px;width:295px;height:45px;background:var(--white);display:flex;align-items:center;gap:14px;padding-left:18px;font-size:12px;color:var(--blue-deep)}
.btn-signup{left:967px;top:2495px;width:100px;height:41px;background:var(--black);font-size:15px}
.bottom-bar{left:0;top:2623px;width:1200px;height:76px;background:var(--blue-mid)}
.follow{left:133px;top:2649px;display:flex;align-items:center;gap:12px;font-size:11px;font-weight:700;color:var(--white)}
.social{width:22px;height:22px;border-radius:50%;background:var(--blue-soft)}
.copyright{right:129px;top:2654px;font-size:10px;color:var(--white)}
</style>
</head>
<body>
<div class="page">

  <!-- Hero -->
  <section class="abs hero" role="img" aria-label="Night view of a city waterfront with lit tower blocks reflected in the water"></section>

  <div class="abs brand"><span class="brand-dot"></span><span>Bright Morrow<br>Ltd</span></div>

  <div class="abs contact-chip" style="left:662px;top:28px">
    <span class="chip-icon">
      <svg width="16" height="12" viewBox="0 0 16 12"><rect x="1" y="1" width="14" height="10" fill="none" stroke="#fff" stroke-width="1.6"/><path d="M1 1l7 6 7-6" fill="none" stroke="#fff" stroke-width="1.6"/></svg>
    </span>
    <span><span class="chip-label">CALL US</span><br><span class="chip-value">info@brightmorrow.co.uk</span></span>
  </div>
  <div class="abs contact-chip" style="left:902px;top:28px">
    <span class="chip-icon">
      <svg width="16" height="16" viewBox="0 0 16 16"><path d="M3 1.5l3 3-1.6 2a9 9 0 0 0 5 5l2-1.6 3 3-1.8 2C7 15 1 9 1.5 3.3z" fill="#fff"/></svg>
    </span>
    <span><span class="chip-label">CALL US</span><br><span class="chip-value strong">(555).0100.2020</span></span>
  </div>

  <nav class="abs main-nav">
    <a class="active" href="#">Home</a>
    <a href="#">About Us</a>
    <a href="#">Services</a>
    <a href="#">Blog</a>
    <a href="#">Testimonials</a>
    <a href="#">Contact Us</a>
  </nav>

  <div class="abs hero-title">
    <h1>Cleaning Services</h1>
    <p>In Warrington</p>
  </div>

  <svg class="abs" style="left:0;top:520px" width="1200" height="90" viewBox="0 0 1200 90">
    <polygon points="0,60 600,14 1200,56 1200,90 0,90" fill="#fff"/>
    <polyline points="0,60 600,14 1200,56" fill="none" stroke="#0455a3" stroke-width="5"/>
  </svg>

  <div class="abs slider-ctrl">
    <svg width="10" height="14" viewBox="0 0 10 14"><path d="M8 1L2 7l6 6" fill="none" stroke="#fff" stroke-width="2"/></svg>
    <svg width="10" height="14" viewBox="0 0 10 14"><path d="M2 1l6 6-6 6" fill="none" stroke="#fff" stroke-width="2"/></svg>
  </div>

  <!-- Services -->
  <h2 class="abs section-title services-title">Our Services</h2>
  <div class="abs rule services-rule"></div>

  <div class="abs divider" style="left:416px"></div>
  <div class="abs divider" style="left:760px"></div>

  <svg width="0" height="0" style="position:absolute">
    <defs>
      <symbol id="i-house" viewBox="0 0 24 24"><path d="M3 11l9-8 9 8v10H3z" fill="none" stroke="#0455a3" stroke-width="2"/><rect x="9" y="14" width="6" height="7" fill="#0455a3"/></symbol>
      <symbol id="i-office" viewBox="0 0 24 24"><rect x="5" y="3" width="14" height="18" fill="none" stroke="#0455a3" stroke-width="2"/><path d="M9 7h2M13 7h2M9 11h2M13 11h2M9 15h2M13 15h2" stroke="#0455a3" stroke-width="2"/></symbol>
      <symbol id="i-window" viewBox="0 0 24 24"><rect x="4" y="4" width="16" height="16" fill="none" stroke="#0455a3" stroke-width="2"/><path d="M12 4v16M4 12h16" stroke="#0455a3" stroke-width="2"/></symbol>
      <symbol id="i-team" viewBox="0 0 24 24"><circle cx="8" cy="9" r="3" fill="#0455a3"/><circle cx="16" cy="9" r="3" fill="#0455a3"/><path d="M2 19c0-4 3-6 6-6s6 2 6 6zM10 19c0-4 3-6 6-6s6 2 6 6z" fill="#0455a3"/></symbol>
      <symbol id="i-floor" viewBox="0 0 24 24"><path d="M4 21L9 3h6l5 18z" fill="none" stroke="#0455a3" stroke-width="2"/><path d="M12 6v3M12 12v3M12 18v2" stroke="#0455a3" stroke-width="2"/></symbol>
      <symbol id="i-roll" viewBox="0 0 24 24"><ellipse cx="8" cy="14" rx="5" ry="5" fill="none" stroke="#0455a3" stroke-width="2"/><path d="M8 9h12v10H8" fill="none" stroke="#0455a3" stroke-width="2"/></symbol>
      <symbol id="i-sparkle" viewBox="0 0 24 24"><path d="M12 2l2 8 8 2-8 2-2 8-2-8-8-2 8-2z" fill="#0455a3"/></symbol>
      <symbol id="i-key" viewBox="0 0 24 24"><circle cx="8" cy="12" r="4" fill="none" stroke="#0455a3" stroke-width="2"/><path d="M12 12h9M18 12v4M21 12v3" stroke="#0455a3" stroke-width="2"/></symbol>
      <symbol id="i-roller" viewBox="0 0 24 24"><rect x="4" y="3" width="14" height="6" rx="1" fill="#0455a3"/><path d="M18 6h2v6h-8v3" fill="none" stroke="#0455a3" stroke-width="2"/><rect x="10" y="15" width="4" height="7" fill="#0455a3"/></symbol>
      <symbol id="i-drop" viewBox="0 0 24 24"><path d="M12 3c4 6 6 9 6 12a6 6 0 0 1-12 0c0-3 2-6 6-12z" fill="none" stroke="#0455a3" stroke-width="2"/></symbol>
      <symbol id="i-home" viewBox="0 0 24 24"><path d="M2 12l10-9 10 9h-3v9H5v-9z" fill="#0455a3"/></symbol>
      <symbol id="i-shop" viewBox="0 0 24 24"><path d="M3 4h18l-1 6H4z" fill="#0455a3"/><rect x="5" y="11" width="14" height="10" fill="none" stroke="#0455a3" stroke-width="2"/></symbol>
    </defs>
  </svg>

  <div class="abs service" style="left:132px;top:665px"><span class="service-icon"><svg width="24" height="24"><use href="#i-house"/></svg></span><span>Housecleaning &amp;<br>Maid Service</span></div>
  <div class="abs service" style="left:132px;top:739px"><span class="service-icon"><svg width="24" height="24"><use href="#i-office"/></svg></span><span>Office &amp; Commercial<br>Cleaning</span></div>
  <div class="abs service" style="left:132px;top:816px"><span class="service-icon"><svg width="24" height="24"><use href="#i-window"/></svg></span><span>Windows, Carpet &amp;<br>Upholstery Cleaning</span></div>
  <div class="abs service" style="left:132px;top:897px"><span class="service-icon"><svg width="24" height="24"><use href="#i-team"/></svg></span><span>Individual or<br>Team Cleaning</span></div>

  <div class="abs service" style="left:487px;top:665px"><span class="service-icon"><svg width="24" height="24"><use href="#i-floor"/></svg></span><span>Floor Cleaning &amp;<br>Restoration</span></div>
  <div class="abs service" style="left:487px;top:739px"><span class="service-icon"><svg width="24" height="24"><use href="#i-roll"/></svg></span><span>Carpet &amp; Upholstery<br>Cleaning</span></div>
  <div class="abs service" style="left:487px;top:816px"><span class="service-icon"><svg width="24" height="24"><use href="#i-sparkle"/></svg></span><span>Deep Cleaning &amp;<br>Disinfection</span></div>
  <div class="abs service" style="left:487px;top:897px"><span class="service-icon"><svg width="24" height="24"><use href="#i-key"/></svg></span><span>End/Beginning Of<br>Tenancy</span></div>

  <div class="abs service" style="left:834px;top:665px"><span class="service-icon"><svg width="24" height="24"><use href="#i-roller"/></svg></span><span>Stone/Marble Maint. &amp;<br>Restoration</span></div>
  <div class="abs service" style="left:834px;top:739px"><span class="service-icon"><svg width="24" height="24"><use href="#i-drop"/></svg></span><span>Pressure Washing</span></div>
  <div class="abs service" style="left:834px;top:816px"><span class="service-icon"><svg width="24" height="24"><use href="#i-home"/></svg></span><span>Clean Domestic</span></div>
  <div class="abs service" style="left:834px;top:897px"><span class="service-icon"><svg width="24" height="24"><use href="#i-shop"/></svg></span><span>Commercial Premises</span></div>

  <!-- Who we are -->
  <div class="abs about-photo" role="img" aria-label="Glass office tower rising against a blue sky"></div>
  <div class="abs about-panel"></div>
  <h2 class="abs about-title">WHO WE ARE</h2>
  <div class="abs rule about-rule"></div>
  <p class="abs about-lead">There are many variations of passages of Lorem Ipsum available, but the majority have suffered.</p>
  <p class="abs about-body">It is a long established fact that a reader will be distracted by the readable content of a page when looking at its layout. The point of using Lorem Ipsum is that it has a more-or-less normal distribution of letters, as opposed to using.</p>
  <a class="abs btn btn-more" href="#">Read More</a>

  <!-- What we do -->
  <section class="abs work"></section>
  <svg class="abs" style="left:0;top:1400px" width="1200" height="70" viewBox="0 0 1200 70">
    <polygon points="0,58 599,13 1200,56 1200,70 0,70" fill="#3176b5"/>
    <polyline points="0,58 599,13 1200,56" fill="none" stroke="#fff" stroke-width="5"/>
  </svg>
  <h2 class="abs section-title work-title">What We Do</h2>
  <div class="abs rule work-rule"></div>

  <div class="abs step-line"></div>

  <div class="abs step-dot" style="left:133px;top:1554px">
    <svg width="24" height="24" viewBox="0 0 24 24"><circle cx="6" cy="12" r="3" fill="#3176b5"/><circle cx="18" cy="5" r="3" fill="#3176b5"/><circle cx="18" cy="19" r="3" fill="#3176b5"/><path d="M6 12L18 5M6 12l12 7" stroke="#3176b5" stroke-width="2"/></svg>
  </div>
  <div class="abs" style="left:250px;top:1556px"><h3 class="step-head">Heading 1</h3><p class="step-text">There are many variations of passages of Lorem Ipsum available.</p></div>

  <div class="abs step-dot" style="left:133px;top:1701px">
    <svg width="24" height="24" viewBox="0 0 24 24"><circle cx="12" cy="12" r="9" fill="none" stroke="#3176b5" stroke-width="2.4"/><path d="M12 7v5h4" fill="none" stroke="#3176b5" stroke-width="2.4"/></svg>
  </div>
  <div class="abs" style="left:250px;top:1703px"><h3 class="step-head">Heading 2</h3><p class="step-text">There are many variations of passages of Lorem Ipsum available.</p></div>

  <div class="abs step-dot" style="left:133px;top:1849px">
    <svg width="24" height="24" viewBox="0 0 24 24"><path d="M4 15v-3a8 8 0 0 1 16 0v3" fill="none" stroke="#3176b5" stroke-width="2.4"/><rect x="3" y="14" width="5" height="7" rx="1" fill="#3176b5"/><rect x="16" y="14" width="5" height="7" rx="1" fill="#3176b5"/></svg>
  </div>
  <div class="abs" style="left:250px;top:1851px"><h3 class="step-head">Heading 3</h3><p class="step-text">There are many variations of passages of Lorem Ipsum available.</p></div>

  <!-- Get quote -->
  <section class="abs quote"></section>
  <h2 class="abs quote-title">GET QUOTE</h2>
  <div class="abs rule quote-rule"></div>
  <p class="abs quote-text">It is a long established fact that a reader will be distracted by the readable content of a page when looking at its layout. The point of using Lorem Ipsum is that it has a more-or</p>

  <div class="abs field" style="left:569px;top:2047px;width:239px;height:43px">Name</div>
  <div class="abs field" style="left:569px;top:2106px;width:239px;height:43px">E mail</div>
  <div class="abs field" style="left:569px;top:2171px;width:239px;height:43px;justify-content:space-between">Cleaning
    <svg width="14" height="8" viewBox="0 0 14 8"><path d="M0 0h14L7 8z" fill="#1b1b1b"/></svg>
  </div>
  <div class="abs field area" style="left:828px;top:2047px;width:241px;height:167px">Message</div>
  <a class="abs btn btn-submit" href="#">Submit</a>

  <!-- Footer -->
  <section class="abs footer"></section>
  <svg class="abs" style="left:0;top:2280px" width="1200" height="80" viewBox="0 0 1200 80">
    <polygon points="0,66 600,18 1200,44 1200,80 0,80" fill="#0455a3"/>
    <polyline points="0,66 600,18 1200,44" fill="none" stroke="#3176b5" stroke-width="6"/>
  </svg>

  <div class="abs brand"><span class="brand-dot"></span><span>Bright Morrow<br>Ltd</span></div>

  <div class="abs" style="left:427px;top:2390px">
    <h4 class="foot-head">Contact Us</h4>
    <ul class="foot-list">
      <li>12 Larkfield Road</li>
      <li>Warrington, WA1 4XY.</li>
      <li>T ; 555.0100.202</li>
      <li>E : hello@brightmorrow.co.uk</li>
    </ul>
  </div>
  <div class="abs" style="left:619px;top:2390px">
    <h4 class="foot-head">Menu</h4>
    <ul class="foot-list">
      <li>Home</li><li>About Us</li><li>Services</li><li>Blog</li><li>Testimonials</li><li>Contact Us</li>
    </ul>
  </div>
  <div class="abs" style="left:770px;top:2390px"><h4 class="foot-head">Newsletter Signup!</h4></div>
  <div class="abs news-field">
    <svg width="14" height="10" viewBox="0 0 14 10"><rect x="0.8" y="0.8" width="12.4" height="8.4" fill="none" stroke="#0455a3" stroke-width="1.4"/><path d="M1 1l6 5 6-5" fill="none" stroke="#0455a3" stroke-width="1.4"/></svg>
    <span>E mail id</span>
  </div>
  <a class="abs btn btn-signup" href="#">Signup!</a>

  <div class="abs bottom-bar"></div>
  <div class="abs follow">FOLLOW US :
    <span class="social"></span><span class="social"></span><span class="social"></span><span class="social"></span>
  </div>
  <p class="abs copyright">Copyrights @ 2016 All Rights Reserved</p>

</div>
</body>
</html>
```